Website Design for Nublora Cloud As a Service

We are building a service to allow customers to own their own private clouds easily and cheaply. Owning your own private cloud saves costs, and offers more flexibility than a public cloud provider but has historically been a complex and expensive option.

We plan to offer a service where we build and maintain your own private cloud on your own hardware for a cheap monthly costs. Similar to this service - https://nimbrovex.com/solutions/private-cloud

We already have a logo and branding in place - we'd like a website design to be tailored from this branding, see attached logo design.

Feel free to add important elements on the home page such as testimonials, client/partner logos, contact form, social media, etc using placeholder contents in addition to the document we attached.

We also plan to add sub-pages in the future so please make sure that your website design has a full navigation menu.

An example of the site we like: https://www.quorvant.com/ we'd be happy for you to take inspiration from this website.

Target Market(s)

B2B focused, we are targeting start-up/small/medium sized companies who needs help with their cloud and IT infrastructure.

Industry/Entity Type

IT

Number of Pages Required

1 page

Font styles to use
Other font styles liked:
• Please refer to the attachment - font must have Mayeka Demi Bold & Retroica

Requirements
Must have
• Please add placeholder menu since we're planning to have subpages later on.

```html
<!DOCTYPE html>
<html lang="en">
<head>
<meta charset="utf-8">
<title>Nublora Cloud – Private Cloud as a Service</title>
<link href="https://fonts.googleapis.com/css2?family=Comfortaa:wght@400;600;700&family=Quicksand:wght@400;500;600;700&display=swap" rel="stylesheet">
<style>
:root{
  --blue:#2f8fd5;
  --blue-dark:#1f6aa5;
  --hero-a:#2a86c6;
  --hero-b:#1c5f97;
  --ink:#333a40;
  --ink-soft:#555d64;
  --pale:#e9f3fb;
  --pale-2:#d9eaf7;
  --line:#cfe2f1;
  --footer:#1c1c1c;
  --white:#ffffff;
}
*{box-sizing:border-box;margin:0;padding:0}
html,body{width:1200px;height:3847px;overflow:hidden}
body{position:relative;background:var(--white);font-family:"Quicksand",sans-serif;color:var(--ink)}
.abs{position:absolute}
h1,h2,h3{font-family:"Comfortaa",sans-serif;font-weight:700}
.accent{color:var(--blue)}

/* header */
.site-header{position:absolute;left:0;top:0;width:1200px;height:78px;background:var(--white)}
.brand{position:absolute;display:flex;align-items:center;gap:10px;font-family:"Comfortaa",sans-serif;font-weight:700;color:var(--blue)}
.brand .dot{width:30px;height:30px;border-radius:50%;background:var(--blue)}
.site-header .brand{left:112px;top:20px;font-size:28px}
.main-nav{position:absolute;left:450px;top:26px;display:flex;gap:24px;font-size:18px;font-weight:500;color:#444}
.search{position:absolute;left:906px;top:26px}
.btn{position:absolute;display:flex;align-items:center;justify-content:center;font-weight:600;font-size:18px;border-radius:4px}
.btn-solid{background:var(--blue);color:var(--white)}
.signup{left:970px;top:16px;width:120px;height:46px}

/* hero */
.hero{position:absolute;left:0;top:78px;width:1200px;height:656px;background:linear-gradient(160deg,var(--hero-a),var(--hero-b));border-radius:0 0 200px 200px/0 0 120px 120px;overflow:hidden}
.hero h1{position:absolute;left:109px;top:124px;width:560px;font-size:34px;line-height:45px;color:var(--white);font-weight:600}
.hero p{position:absolute;left:112px;width:520px;font-size:16px;line-height:28px;color:var(--white)}
.hero .lead{top:276px}
.hero .ask{top:378px;font-weight:700}
.btn-outline{border:2px solid var(--white);color:var(--white);left:112px;top:462px;width:127px;height:45px;font-weight:500}
.hero-art{position:absolute;left:620px;top:86px;width:500px;height:500px;border-radius:40px;background:linear-gradient(135deg,rgba(190,225,250,.55),rgba(40,110,170,.35))}

/* benefits */
.section-title{position:absolute;left:0;width:1200px;text-align:center;font-size:40px;line-height:46px;color:#555}
.rule{position:absolute;height:3px;background:var(--blue)}
.rule.grey{background:#777}
.benefit-icon{position:absolute;width:73px;height:73px;border-radius:6px;background:linear-gradient(160deg,#3a8fcb,#1e6aa6);display:flex;align-items:center;justify-content:center}
.benefit{position:absolute;width:300px;font-size:14px;line-height:24px;color:var(--ink)}
.benefit h3{font-family:"Quicksand",sans-serif;font-weight:500;font-size:16px;color:var(--blue);line-height:22px;margin-bottom:4px}
.benefit.left{text-align:right;left:31px}
.benefit.right{left:882px;width:240px}
.hub{position:absolute;left:469px;top:1029px;width:262px;height:262px;border-radius:50%;background:#f4f6f8;box-shadow:0 0 18px rgba(0,0,0,.08)}
.hub-inner{position:absolute;left:19px;top:19px;width:224px;height:224px;border-radius:50%;background:var(--white);box-shadow:0 4px 14px rgba(0,0,0,.12);display:flex;flex-direction:column;align-items:center;justify-content:center;gap:10px}
.hub-inner .brand{position:static;font-size:20px;flex-direction:column;gap:8px}
.connectors{position:absolute;left:0;top:950px}

/* transformation */
.transform{position:absolute;left:0;top:1455px;width:1200px;height:682px;background:var(--pale);border-radius:0 0 160px 160px/0 0 110px 110px}
.transform h2{position:absolute;left:110px;top:60px;font-size:44px;line-height:52px;color:#555;width:560px}
.body-text{position:absolute;font-size:16px;line-height:28px;color:var(--ink)}
.body-text p{margin-bottom:8px}
.feature{position:absolute;width:190px;height:185px;background:var(--white);border-radius:6px 6px 40px 6px;box-shadow:0 6px 16px rgba(40,90,140,.12);display:flex;flex-direction:column;align-items:center;justify-content:flex-end;padding-bottom:36px;gap:20px;font-size:21px;font-weight:500;color:var(--ink)}
.feature.on{background:var(--blue);color:var(--white)}
.feature .blob{width:120px;height:70px;border-radius:40px;background:#eef2f5;display:flex;align-items:center;justify-content:center}
.feature.on .blob{background:rgba(255,255,255,.18)}

/* public cloud */
.public-art{position:absolute;left:15px;top:2261px;width:492px;height:403px;border-radius:30px;background:linear-gradient(135deg,#eaf4fc,#bcdcf3)}
.public h2{position:absolute;left:524px;top:2218px;font-size:42px;line-height:51px;color:var(--blue);font-weight:600}
.public .body-text{left:525px;top:2358px;width:580px}
.public .body-text p{margin-bottom:10px}

/* difference */
.difference{position:absolute;left:0;top:2783px;width:1200px;height:615px;background:var(--pale-2)}
.difference h2{position:absolute;left:0;width:1200px;top:70px;text-align:center;font-size:42px;color:var(--blue);font-weight:600}
.diff-item{position:absolute;width:400px;padding-left:32px;font-size:16px;line-height:28px;color:var(--ink)}
.diff-item::before{content:"";position:absolute;left:0;top:8px;width:18px;height:11px;border-radius:6px;background:var(--blue)}

/* footer */
.site-footer{position:absolute;left:0;top:3398px;width:1200px;height:449px;background:var(--footer);border-radius:90px 90px 0 0;color:var(--white)}
.site-footer .brand{left:0;width:1200px;justify-content:center;top:78px;font-size:30px;color:var(--white)}
.site-footer .brand .dot{background:var(--blue)}
.fcol{position:absolute;top:176px;font-size:16px;line-height:30px}
.fcol h4{font-family:"Quicksand",sans-serif;font-weight:600;font-size:19px;margin-bottom:6px}
.fcol li{list-style:none;display:flex;align-items:center;gap:8px}
.footer-rule{position:absolute;left:112px;top:381px;width:1088px;height:1px;background:#555}
.copyright{position:absolute;left:0;width:1200px;top:404px;text-align:center;font-size:15px}
</style>
</head>
<body>

<header class="site-header">
  <div class="brand"><span class="dot"></span>Nublora Cloud</div>
  <nav class="main-nav"><span>Home</span><span>About</span><span>Products</span><span>Solutions</span><span>Pricing</span></nav>
  <svg class="search" width="26" height="26" viewBox="0 0 26 26"><circle cx="11" cy="11" r="8" fill="none" stroke="#222" stroke-width="2.2"/><line x1="17" y1="17" x2="24" y2="24" stroke="#222" stroke-width="2.4"/></svg>
  <div class="btn btn-solid signup">Sign Up</div>
</header>

<section class="hero">
  <h1>A groundbreaking way for your small business to benefit from the power of the cloud</h1>
  <p class="lead">Nublora Cloud as a Service is here to help small businesses utilise the power of the cloud without complicated set-ups or scary price tags</p>
  <p class="ask">Ready to modernise your infrastructure with a fully managed private cloud solution from NCaaS?</p>
  <div class="btn btn-outline">Contact Us</div>
  <div class="hero-art" role="img" aria-label="Isometric illustration of a desktop computer, laptop and server racks on a cloud"></div>
</section>

<h2 class="section-title" style="top:802px">How <span class="accent">NCAAS benefits</span><br><span class="accent">your business</span></h2>
<div class="rule grey" style="left:552px;top:911px;width:97px"></div>

<svg class="connectors" width="1200" height="420" viewBox="0 0 1200 420">
  <g fill="none" stroke="#cfe2f1" stroke-width="2">
    <path d="M422 45 H500 L542 92"/><path d="M787 45 H700 L658 92"/>
    <path d="M422 210 H469"/><path d="M787 210 H731"/>
    <path d="M422 345 H500 L542 300"/><path d="M787 345 H700 L658 300"/>
  </g>
</svg>

<div class="benefit left" style="top:963px"><h3>Totally flexible</h3>Get the cloud you want and the latest innovations you need</div>
<div class="benefit-icon" style="left:349px;top:967px"><svg width="42" height="42" viewBox="0 0 42 42" fill="none" stroke="#fff" stroke-width="2"><circle cx="21" cy="21" r="7"/><path d="M21 4v6M21 32v6M4 21h6M32 21h6M9 9l4 4M29 29l4 4M33 9l-4 4M13 29l-4 4"/></svg></div>
<div class="benefit left" style="top:1108px"><h3>Faster</h3>Our private cloud solutions outpace public clouds</div>
<div class="benefit-icon" style="left:349px;top:1113px"><svg width="42" height="42" viewBox="0 0 42 42" fill="none" stroke="#fff" stroke-width="2"><circle cx="23" cy="23" r="13"/><path d="M23 23l6-6M20 6h6M4 18h8M6 24h6M8 30h5"/></svg></div>
<div class="benefit left" style="top:1253px"><h3>Greater value for money</h3>Totally transparent pricing for no nasty month-end surprises</div>
<div class="benefit-icon" style="left:349px;top:1258px"><svg width="42" height="42" viewBox="0 0 42 42" fill="none" stroke="#fff" stroke-width="2"><circle cx="22" cy="13" r="8"/><path d="M22 8v10M4 30l8-5h10l-4 4M12 36l6-4h14l6-8"/></svg></div>

<div class="benefit-icon" style="left:787px;top:967px"><svg width="42" height="42" viewBox="0 0 42 42" fill="none" stroke="#fff" stroke-width="2"><circle cx="21" cy="21" r="15"/><circle cx="21" cy="21" r="10"/><path d="M10 32L32 10"/></svg></div>
<div class="benefit right" style="top:963px"><h3>No consultancy fees</h3>We'll work with you and charge set fees for everything</div>
<div class="benefit-icon" style="left:787px;top:1113px"><svg width="42" height="42" viewBox="0 0 42 42" fill="none" stroke="#fff" stroke-width="2"><circle cx="24" cy="14" r="7"/><path d="M4 30l8-5h10l-4 4M12 36l6-4h14l6-8"/></svg></div>
<div class="benefit right" style="top:1108px"><h3>Management, monitoring and maintenance</h3>They're all included in your monthly price</div>
<div class="benefit-icon" style="left:787px;top:1258px"><svg width="42" height="42" viewBox="0 0 42 42" fill="none" stroke="#fff" stroke-width="2"><path d="M6 18h7v18H6zM13 20l6-12c3 0 4 2 3 6h10c2 0 3 2 2 4l-3 13c-1 2-2 3-4 3H13"/></svg></div>
<div class="benefit right" style="top:1253px"><h3>Tried &amp; tested cloud solutions</h3>we'll deploy the right OpenGrid solutions for your business</div>

<div class="hub"><div class="hub-inner"><div class="brand"><span class="dot"></span>Nublora Cloud</div></div></div>

<section class="transform">
  <h2><span class="accent">NCAAS</span> can drive your digital transformation today</h2>
  <div class="rule" style="left:112px;top:232px;width:115px"></div>
  <div class="body-text" style="left:110px;top:266px;width:490px">
    <p>Organisations of all shapes and sizes are reaping the time and money saving benefits that the cloud brings.</p>
    <p>But for small businesses seeking to transition, managing the time and financial costs of transitioning, and knowing whether to opt for a public or private cloud can cause you to hit the pause button.</p>
    <p>NCAAS is here to help you switch on your cloud transformation in a way that works best for you.&nbsp; We deliver and support fully managed private cloud solutions that are:</p>
  </div>
  <div class="btn btn-solid" style="left:110px;top:563px;width:136px;height:45px">Get started</div>

  <div class="feature on" style="left:690px;top:123px"><div class="blob"><svg width="44" height="44" viewBox="0 0 44 44" fill="none" stroke="#fff" stroke-width="2"><path d="M14 30L30 8c4-2 6 0 6 6L20 34zM14 30l-6 2 2-8 6-2M20 34l-2 6 8-4"/><circle cx="28" cy="16" r="3"/></svg></div>Fast</div>
  <div class="feature" style="left:900px;top:166px"><div class="blob"><svg width="44" height="44" viewBox="0 0 44 44" fill="none" stroke="#2f8fd5" stroke-width="2"><circle cx="22" cy="22" r="13"/><path d="M16 22l4 4 8-8"/></svg></div>Easy</div>
  <div class="feature" style="left:690px;top:329px"><div class="blob"><svg width="44" height="44" viewBox="0 0 44 44" fill="none" stroke="#2f8fd5" stroke-width="2"><path d="M12 20v-6h5v6M17 14V10h5v10M22 12h5v10M27 16h5v10c0 8-4 12-10 12h-2c-5 0-8-4-8-10v-8"/></svg></div>Powerful</div>
  <div class="feature" style="left:900px;top:372px"><div class="blob"><svg width="44" height="44" viewBox="0 0 44 44" fill="none" stroke="#2f8fd5" stroke-width="2"><rect x="8" y="8" width="28" height="28" rx="2"/><path d="M16 28l12-12M20 16h8v8"/></svg></div>Scalable</div>
</section>

<section class="public">
  <div class="public-art" role="img" aria-label="Isometric illustration of a cloud data centre with people working on devices"></div>
  <h2>If you're using a public<br>cloud now…</h2>
  <div class="rule grey" style="left:524px;top:2327px;width:97px"></div>
  <div class="body-text">
    <p><span class="accent">You could be paying too much…</span> Public cloud pricing structures have a habit of sneakily scaling up very quickly. With NCAAS, you'll always know what you're paying for your private cloud services.</p>
    <p><span class="accent">You're likely not getting the benefits of full functionality…</span> Public cloud providers cannot adopt new innovations and functions as quickly and easily as the private cloud solutions you'll get from NCAAS.</p>
    <p><span class="accent">You'll be tied to the services your provider can provide…</span> Public cloud providers cannot adopt new innovations and functions as quickly and easily as the private cloud solutions you'll get from NCAAS.</p>
  </div>
  <div class="btn btn-solid" style="left:525px;top:2651px;width:119px;height:45px">Let's Talk</div>
</section>

<section class="difference">
  <h2>The NCAAS Difference</h2>
  <div class="diff-item" style="left:111px;top:190px">We'll quickly get to grips with what your organisation needs, and deliver it via our private cloud solutions.</div>
  <div class="diff-item" style="left:111px;top:284px">Enjoy the ease of the public cloud, combined with the features, innovations and flexibility of the private cloud.</div>
  <div class="diff-item" style="left:111px;top:387px">You can focus on your core business while we support you with a dedicated cloud infrastructure.</div>
  <div class="diff-item" style="left:111px;top:481px">We'll create and deliver the launchpad that will take your business forward.</div>
  <div class="diff-item" style="left:651px;top:190px;width:450px">Get the benefits of your own cloud infrastructure and reduce your operational costs.</div>
  <div class="diff-item" style="left:651px;top:284px;width:450px">Fast and easy computing, storage and network resources.</div>
  <div class="diff-item" style="left:651px;top:387px;width:450px">Managed operations from private OpenGrid clouds and Kontainerd.</div>
  <div class="diff-item" style="left:651px;top:481px;width:450px">We'll support your growth and scale your cloud as you need it.</div>
</section>

<footer class="site-footer">
  <div class="brand"><span class="dot"></span>Nublora Cloud</div>
  <div class="fcol" style="left:112px">
    <h4>CONTACT</h4>
    <ul>
      <li><svg width="12" height="16" viewBox="0 0 12 16"><path d="M6 0a6 6 0 0 0-6 6c0 4 6 10 6 10s6-6 6-10a6 6 0 0 0-6-6z" fill="#fff"/><circle cx="6" cy="6" r="2" fill="#1c1c1c"/></svg>Nublora Cloud,</li>
      <li style="padding-left:20px">Address comes here</li>
      <li style="margin-top:14px"><svg width="14" height="14" viewBox="0 0 14 14"><path d="M3 0l3 3-2 2c1 2 3 4 5 5l2-2 3 3-2 3C6 14 0 8 0 2z" fill="#fff"/></svg>+1 555-010-2040</li>
      <li style="margin-top:14px"><svg width="16" height="12" viewBox="0 0 16 12"><rect width="16" height="12" rx="1" fill="#fff"/><path d="M0 1l8 6 8-6" stroke="#1c1c1c" stroke-width="1.4" fill="none"/></svg>hello@nublora.example</li>
    </ul>
  </div>
  <div class="fcol" style="left:418px">
    <h4>QUICK LINKS</h4>
    <ul><li>Home</li><li>About</li><li>Products</li><li>Solutions</li><li>Pricing</li></ul>
  </div>
  <div class="fcol" style="left:664px">
    <h4>OTHER LINKS</h4>
    <ul><li>Status page</li><li>Docs</li><li>Release Notes</li><li>Privacy &amp; Terms of Use</li><li>Contact Support</li></ul>
  </div>
  <div class="fcol" style="left:978px">
    <h4>FOLLOW US</h4>
    <ul>
      <li><svg width="14" height="14"><rect width="14" height="14" rx="2" fill="#fff"/></svg>Friendsphere</li>
      <li><svg width="14" height="14"><rect width="14" height="14" rx="2" fill="#fff"/></svg>Chirpline</li>
      <li><svg width="14" height="14"><rect width="14" height="14" rx="2" fill="#fff"/></svg>Workmesh</li>
    </ul>
  </div>
  <div class="footer-rule"></div>
  <div class="copyright">2022 Nublora Cloud. All Rights Reserved.</div>
</footer>

</body>
</html>
```